Sedona Themed Wedding Invitation & RSVP

*We have added our "Save the Date" for reference. We are not looking for an exact match, but we'd like the invitation and the "Save the Date" to coordinate. Our wedding colors are light pink, light green, cream, and gold. We have also added pictures of bouquets to give you an idea of the color palette and also examples of flowers and greenery to use in the invitation. What we like about the "Save the Date" is that it draws on the wedding colors and brings them in through the colors of the sunset.
*We have also added additional pictures the venue, the Maison Pellerin Lodge, and several maps. We hope that you can use these to get a better feel for our venue and the theme of our wedding. It will be soft and romantic and at the very height of spring.
* We appreciated that many designers incorporated the Lodge at Maison Pellerin, we'd like to see more of that.
*Please note that we included some photos of Sedona for inspiration, please do not feel tied to these, do your own research and find what works best with your design.
*These maps are being included as references, but they are the work of other artists. Please make your own map from scratch and use these as references.
We would like a vertical quad-fold wedding invitation that has a perforated edge RSVP which can be sent as a postcard.
We have attached pictures of a similar style of invitation to serve as an example of the overall style we are looking for. We would like to see the end project be in a similar style of watercolor, but it would be Sedona themed throughout (rather than the forest theme presented in the attached example). We have also attached pictures of Sedona to serve as further inspiration. Below, we have provided an outline organized by panel (four panels on the front and four panels on the back) with descriptions of the more specific details:
-Front four panels:
-Panel 1: "Please join us for the wedding of Tobias and Colette"
-Panel 2: "Come out and celebrate. [INSERT TIME OF WEDDING HERE]
Saturday, May First 2021 at Maison Pellerin Resort"
-Panel 3: Custom map of Sedona. Include Maison Pellerin Resort on the
map (exemplar picture is of an idea for this is also included below)
- Panel 4: RSVP similar to one in the exemplar invitation. For RSVP date
deadline use April 1st, 2021. Address is 2738 E Marlow Ave Phoenix, AZ
85016
-Back four panels:
-Panel 1: Venue: Maison Pellerin Resort. 118 Fennick Way, Sedona, AZ 86351.
Please arrive no earlier than XXX PM when valet services begin. Dinner
and dancing to follow the ceremony
-Panel 2: Hotels: Maison Pellerin Resort 118 Fennick Way, Sedona, AZ 86351
(800) 555-0193; Wrenfield Inn 612 S Halvern Rd, Sedona, AZ 86351
(855) 555-0148.
"Hotel reservations can also be made through the links provided on our
website"
- Panel 3: "We have reserved a block of rooms for our guests. Please
mention the Thorne Pellow Wedding when you call to reserve."
"For additional details, please visit our wedding website and take a walk
down memory lane with us as we prepare to celebrate the rest of our
lives together: [INSERT WEDDING WEBSITE HERE AND
PASSWORD]"
- Panel 4: "Ceremony and celebration will be outdoors. Semi-formal attire
and flat shoes are recommended."
"Additionally, although we love your children, we want our wedding to
be your night off! Please know space is very limited; accordingly, we
encourage a weekend getaway for the grownups."
We'd like to have a succulent and rose at the bottom of the panel (an
exemplar picture is of an idea for this is also included below)
Updates
We have given extensive feedback to designers and would like to give them time to adjust their designs. Additionally, we have incorporated a lot more images into the brief that we hope will help!

```html
<!DOCTYPE html>
<html lang="en">
<head>
<meta charset="UTF-8">
<title>RSVP Postcard – Tobias and Colette</title>
<link rel="stylesheet" href="https://fonts.googleapis.com/css2?family=IM+Fell+English+SC&family=Playball&family=Great+Vibes&display=swap">
<style>
  :root {
    --plum: #5e1a48;
    --paper: #f3eac2;
    --paper-light: #f7f0d2;
    --paper-warm: #ecdcaa;
    --hole: #fbf8ec;
    --hole-edge: #c8b98e;
    --sprig: #6a2453;
  }
  html, body {
    margin: 0;
    padding: 0;
    width: 1200px;
    height: 800px;
    overflow: hidden;
    background: var(--paper);
  }
  .postcard {
    position: relative;
    width: 1200px;
    height: 800px;
    overflow: hidden;
    color: var(--plum);
    font-family: "IM Fell English SC", Georgia, serif;
    background:
      radial-gradient(ellipse 420px 260px at 430px 400px, var(--paper-warm) 0%, transparent 70%),
      radial-gradient(ellipse 500px 300px at 950px 250px, var(--paper-light) 0%, transparent 70%),
      radial-gradient(ellipse 380px 260px at 1100px 720px, #efe2b6 0%, transparent 70%),
      var(--paper);
  }
  .perforation {
    position: absolute;
    top: 0;
    width: 16px;
    height: 800px;
  }
  .perforation--left { left: 5px; }
  .perforation--right { right: 5px; }

  .respond-arc {
    position: absolute;
    left: 130px;
    top: 30px;
    width: 290px;
    height: 90px;
  }
  .respond-arc text {
    font-family: "IM Fell English SC", Georgia, serif;
    font-size: 24px;
    fill: var(--plum);
    letter-spacing: 1px;
  }
  .sprig {
    position: absolute;
    background: var(--sprig);
    border-radius: 40% 40% 2px 2px;
  }
  .sprig--date-left { left: 80px; top: 128px; width: 10px; height: 48px; }
  .sprig--date-right { left: 445px; top: 127px; width: 10px; height: 48px; }
  .sprig--arc-left { left: 146px; top: 80px; width: 20px; height: 8px; border-radius: 4px; transform: rotate(-28deg); }
  .sprig--arc-right { left: 382px; top: 92px; width: 20px; height: 8px; border-radius: 4px; transform: rotate(28deg); }

  .deadline { position: absolute; margin: 0; line-height: 1; }
  .deadline__month {
    left: 115px; top: 122px;
    font-family: "Great Vibes", cursive;
    font-size: 46px;
  }
  .deadline__day {
    left: 258px; top: 104px;
    font-size: 80px;
  }
  .deadline__suffix {
    left: 280px; top: 112px;
    font-size: 20px;
  }
  .deadline__year {
    left: 352px; top: 126px;
    font-family: "Great Vibes", cursive;
    font-size: 40px;
  }

  .guest-name__prefix {
    position: absolute;
    left: 74px; top: 248px;
    margin: 0;
    font-size: 58px;
    line-height: 1;
  }
  .write-line {
    position: absolute;
    height: 3px;
    background: var(--plum);
  }
  .write-line--name { left: 133px; top: 298px; width: 529px; }
  .write-line--extra { left: 75px; top: 374px; width: 586px; }

  .reply {
    position: absolute;
    left: 72px;
    display: flex;
    align-items: baseline;
    margin: 0;
    white-space: nowrap;
  }
  .reply--yes { top: 482px; }
  .reply--no { top: 580px; }
  .reply__box {
    width: 30px; height: 28px;
    border: 3px solid var(--plum);
    margin-right: 26px;
    align-self: center;
    transform: translateY(6px);
  }
  .reply__answer {
    font-size: 54px;
    line-height: 1;
    margin-right: 8px;
  }
  .reply__phrase {
    font-family: "Playball", cursive;
    font-size: 48px;
    line-height: 1;
  }

  .divider {
    position: absolute;
    left: 712px; top: 120px;
    width: 3px; height: 632px;
    background: var(--plum);
  }

  .return-address {
    position: absolute;
    left: 715px; right: 0;
    top: 262px;
    text-align: center;
  }
  .return-address__names {
    margin: 0;
    font-size: 48px;
    line-height: 1.1;
    letter-spacing: 1px;
  }
  .return-address__street {
    margin: 22px 0 0;
    font-size: 31px;
    line-height: 1.55;
  }
</style>
</head>
<body>
<main class="postcard">
  <svg class="perforation perforation--left" viewBox="0 0 16 800" aria-hidden="true">
    <defs>
      <pattern id="holes" width="16" height="27.6" patternUnits="userSpaceOnUse" y="-1">
        <circle cx="8" cy="14" r="6.3" fill="var(--hole)" stroke="var(--hole-edge)" stroke-width="0.8"/>
      </pattern>
    </defs>
    <rect width="16" height="800" fill="url(#holes)"/>
  </svg>
  <svg class="perforation perforation--right" viewBox="0 0 16 800" aria-hidden="true">
    <rect width="16" height="800" fill="url(#holes)"/>
  </svg>

  <section class="reply-side">
    <svg class="respond-arc" viewBox="0 0 290 90" aria-label="Please respond by">
      <defs>
        <path id="respond-curve" d="M25 85 Q145 -10 270 85"/>
      </defs>
      <text><textPath href="#respond-curve" startOffset="50%" text-anchor="middle">Please Respond By</textPath></text>
    </svg>
    <div class="sprig sprig--arc-left" role="img" aria-label="small leaf sprig"></div>
    <div class="sprig sprig--arc-right" role="img" aria-label="small leaf sprig"></div>

    <div class="sprig sprig--date-left" role="img" aria-label="leaf sprig ornament"></div>
    <p class="deadline deadline__month">April</p>
    <p class="deadline deadline__day">1</p>
    <p class="deadline deadline__suffix">ST</p>
    <p class="deadline deadline__year">2021</p>
    <div class="sprig sprig--date-right" role="img" aria-label="leaf sprig ornament"></div>

    <p class="guest-name__prefix">M</p>
    <div class="write-line write-line--name"></div>
    <div class="write-line write-line--extra"></div>

    <p class="reply reply--yes">
      <span class="reply__box"></span>
      <span class="reply__answer">YES!</span>
      <span class="reply__phrase">so delighted to attend</span>
    </p>
    <p class="reply reply--no">
      <span class="reply__box"></span>
      <span class="reply__answer">NO!</span>
      <span class="reply__phrase">regretfully decline</span>
    </p>
  </section>

  <div class="divider"></div>

  <address class="return-address">
    <p class="return-address__names">Tobias and Colette</p>
    <p class="return-address__street">2738 E Marlow<br>Ave Phoenix, AZ 85016</p>
  </address>
</main>
</body>
</html>
```